Website Design Request - Management Consulting Firm

We need a Website designed for an IT Management Staffing and Recruiting firm called TRAVENOK based in San Francisco.

The firm is an high-end technology staffing agency. Our focus is on quality and high-caliber candidates rather than quantity.

The website will have two main home pages. One for the recruiter and another on for the candidates.

The website needs to optimize for mobile devices as well.

I have attached few mock-ups that I have done just to show what I am thinking. The UI needs to be very clean, fluid, and it needs to have a modern, rustic, professional feel to it.

Target Market(s)

Technology Manager, Director, VP, CIO of Companies that have $4b-10b dollar revenue. Such as larkspurdwellings.example , https://www.velmorian.example/, quillnet.example, zib.example

Industry/Entity Type

Management Consulting

Number of Pages Required

5+ page

Font styles to use
Sans Serif

Colors
f37122
ffffff

Requirements
Must have
• Please review mock-ups for suggestions
Nice to have
Should not have

```html
<!DOCTYPE html>
<html lang="en">
<head>
<meta charset="utf-8">
<title>TRAVENOK – IT Project Management Jobs</title>
<link href="https://fonts.googleapis.com/css2?family=Jost:wght@400;500;600&family=Lato:wght@400;700&display=swap" rel="stylesheet">
<style>
  :root {
    --orange: #f37122;
    --white: #ffffff;
    --ink: #2b2b2b;
    --muted: #6b6b6b;
    --slate: #464953;
    --pale: #efefef;
    --footer: #f2f2f2;
    --line: #dddddd;
    --hero-dark: #6f6f6f;
    --hero-light: #b9b9b9;
  }
  * { box-sizing: border-box; margin: 0; padding: 0; }
  html, body { width: 672px; height: 1200px; overflow: hidden; background: var(--white); }
  body { position: relative; font-family: "Lato", Arial, sans-serif; color: var(--ink); }
  .abs { position: absolute; }

  /* Header */
  .brand { left: 74px; top: 10px; }
  .brand-name { font-family: "Jost", Arial, sans-serif; font-weight: 500; font-size: 28px; letter-spacing: 1px; color: var(--orange); line-height: 1; }
  .brand-tag { font-family: "Lato", Arial, sans-serif; font-size: 7.4px; letter-spacing: 0.4px; color: var(--ink); margin-top: 3px; }
  .nav-link { top: 22px; font-family: "Jost", Arial, sans-serif; font-size: 9.5px; font-weight: 500; color: var(--ink); }
  .btn-signin, .btn-signup { top: 18px; width: 57px; height: 20px; font-family: "Jost", Arial, sans-serif; font-size: 9px; display: flex; align-items: center; justify-content: center; gap: 4px; }
  .btn-signin { left: 469px; border: 1px solid var(--orange); color: var(--orange); }
  .btn-signup { left: 541px; background: var(--orange); color: var(--white); }

  /* Hero */
  .hero { left: 0; top: 54px; width: 672px; height: 311px; background: linear-gradient(180deg, var(--hero-light) 0%, #9a9a9a 55%, var(--hero-dark) 100%); }
  .hero-title { left: 0; width: 672px; top: 86px; text-align: center; font-family: "Jost", Arial, sans-serif; font-size: 21px; color: var(--white); }
  .hero-title strong { font-weight: 600; }
  .hero-sub { left: 0; width: 672px; top: 119px; text-align: center; font-family: "Jost", Arial, sans-serif; font-size: 11px; color: var(--white); }
  .email-field { left: 174px; top: 154px; width: 324px; height: 37px; background: var(--white); border: 2px solid #e6e6e6; outline: 1px solid var(--white); display: flex; align-items: center; padding-left: 14px; gap: 8px; font-size: 7.5px; color: var(--ink); }
  .btn-offers { left: 268px; top: 214px; width: 135px; height: 37px; background: var(--orange); color: var(--white); font-family: "Jost", Arial, sans-serif; font-weight: 500; font-size: 11px; letter-spacing: 0.4px; display: flex; align-items: center; justify-content: center; box-shadow: 0 3px 6px rgba(0,0,0,0.2); }
  .btn-ghost { top: 307px; height: 22px; border: 1px solid var(--white); color: var(--white); font-family: "Jost", Arial, sans-serif; font-size: 7.5px; display: flex; align-items: center; justify-content: center; }

  /* Tabs */
  .tab { top: 408px; height: 34px; font-family: "Jost", Arial, sans-serif; font-size: 11px; display: flex; align-items: center; justify-content: center; gap: 7px; }
  .tab-active { left: 190px; width: 140px; border: 1px solid var(--orange); color: var(--orange); }
  .tab-active::after { content: ""; position: absolute; left: 64px; bottom: -5px; width: 8px; height: 8px; background: var(--white); border-right: 1px solid var(--orange); border-bottom: 1px solid var(--orange); transform: rotate(45deg); }
  .tab-plain { left: 342px; width: 139px; border: 1px solid var(--slate); color: var(--ink); }

  .steps-title { left: 0; width: 672px; top: 474px; text-align: center; font-family: "Jost", Arial, sans-serif; font-size: 16px; color: var(--orange); letter-spacing: 0.3px; }
  .steps-sub { left: 0; width: 672px; top: 504px; text-align: center; font-family: "Jost", Arial, sans-serif; font-size: 9px; color: var(--muted); }

  .steps-graphic { left: 0; top: 0; }
  .step-text h3 { font-family: "Jost", Arial, sans-serif; font-weight: 500; font-size: 8.5px; color: var(--ink); margin-bottom: 6px; }
  .step-text p { font-family: "Jost", Arial, sans-serif; font-size: 7px; line-height: 11px; color: var(--muted); }
  .step-1 { left: 386px; top: 608px; }
  .step-2 { left: 100px; width: 186px; top: 714px; text-align: right; }
  .step-3 { left: 386px; top: 837px; }

  .btn-upload { left: 250px; top: 958px; width: 158px; height: 32px; background: var(--orange); color: var(--white); font-family: "Jost", Arial, sans-serif; font-weight: 500; font-size: 10px; letter-spacing: 0.3px; display: flex; align-items: center; justify-content: center; gap: 8px; }

  /* Footer */
  .footer { left: 0; top: 1035px; width: 672px; height: 165px; background: var(--footer); }
  .footer-brand { left: 74px; top: 1066px; }
  .footer-brand .brand-name { font-size: 31px; }
  .footer-brand .brand-tag { font-size: 8.4px; }
  .footer-heading { top: 1063px; font-family: "Jost", Arial, sans-serif; font-weight: 500; font-size: 7.5px; color: var(--orange); }
  .contact-row { left: 313px; display: flex; gap: 12px; font-family: "Jost", Arial, sans-serif; font-size: 6.8px; line-height: 11px; color: var(--ink); }
  .social { top: 1085px; width: 24px; height: 24px; border: 1px solid #5a5fa8; border-radius: 50%; background: var(--white); }
  .footer-rule { left: 74px; top: 1150px; width: 524px; height: 1px; background: var(--line); }
  .copyright { left: 0; width: 672px; top: 1171px; text-align: center; font-family: "Jost", Arial, sans-serif; font-size: 6.5px; color: var(--ink); }
</style>
</head>
<body>

<!-- Header -->
<div class="abs brand">
  <div class="brand-name">TRAVENOK</div>
  <div class="brand-tag">PROJECT MANAGEMENT CONSULTING</div>
</div>
<div class="abs nav-link" style="left:337px">Professionals</div>
<div class="abs nav-link" style="left:410px">Employers</div>
<div class="abs btn-signin">
  <svg width="7" height="8" viewBox="0 0 7 8"><rect x="0.5" y="3.5" width="6" height="4.5" fill="#f37122"/><path d="M1.8 3.5V2.4a1.7 1.7 0 0 1 3.4 0v1.1" fill="none" stroke="#f37122" stroke-width="1"/></svg>
  Sign In
</div>
<div class="abs btn-signup">
  <svg width="8" height="8" viewBox="0 0 8 8"><rect x="0.5" y="1.5" width="6" height="6" fill="none" stroke="#fff" stroke-width="0.9"/><path d="M3 5l4-4" stroke="#fff" stroke-width="1.2"/></svg>
  Sign Up
</div>

<!-- Hero -->
<div class="abs hero" role="img" aria-label="Photo of six smiling professionals seated in a row against a white brick wall"></div>
<h1 class="abs hero-title" style="font-weight:400">Looking for <strong>IT Project Mangement</strong> Jobs?</h1>
<p class="abs hero-sub">Upload your resume, accept interview requests, get offers</p>
<div class="abs email-field">
  <svg width="8" height="6" viewBox="0 0 8 6"><rect x="0.5" y="0.5" width="7" height="5" fill="none" stroke="#2b2b2b" stroke-width="0.9"/><path d="M0.5 0.8L4 3.4 7.5 0.8" fill="none" stroke="#2b2b2b" stroke-width="0.9"/></svg>
  Your Email Address
</div>
<div class="abs btn-offers">GET OFFERS NOW</div>
<div class="abs btn-ghost" style="left:217px;width:101px">Looking for Talents?</div>
<div class="abs btn-ghost" style="left:329px;width:139px">See how it works for Employers</div>

<!-- Tabs -->
<div class="abs tab tab-active">
  <svg width="9" height="9" viewBox="0 0 10 10"><circle cx="5" cy="5" r="3.4" fill="none" stroke="#f37122" stroke-width="2.2" stroke-dasharray="1.6 1"/><circle cx="5" cy="5" r="1" fill="#f37122"/></svg>
  How it Works?
</div>
<div class="abs tab tab-plain">
  <svg width="9" height="9" viewBox="0 0 10 10"><circle cx="5" cy="5" r="4.5" fill="#f37122"/></svg>
  Why us?
</div>

<h2 class="abs steps-title" style="font-weight:400">3 SIMPLE STEPS</h2>
<p class="abs steps-sub">Employers pay 25% more for a better FIT Project Manager</p>

<!-- Steps path -->
<svg class="abs steps-graphic" width="672" height="1000" viewBox="0 0 672 1000">
  <defs>
    <filter id="soft-shadow" x="-30%" y="-30%" width="160%" height="160%">
      <feDropShadow dx="0" dy="2" stdDeviation="2.5" flood-color="#000" flood-opacity="0.18"/>
    </filter>
  </defs>
  <path d="M339 550 A72 72 0 0 0 339 694 L339 662 A40 40 0 0 1 339 582 Z" fill="#efefef" stroke="#e2e2e2" stroke-width="0.6"/>
  <path d="M339 662 A72 72 0 0 1 339 806 L339 774 A40 40 0 0 0 339 694 Z" fill="#f37122"/>
  <path d="M339 774 A72 72 0 0 0 339 918 L339 886 A40 40 0 0 1 339 806 Z" fill="#464953"/>

  <text x="282" y="622" transform="rotate(-80 282 622)" text-anchor="middle" font-family="Jost, Arial, sans-serif" font-size="7" font-weight="500" fill="#2b2b2b" letter-spacing="0.5">STEP 1</text>
  <text x="396" y="738" transform="rotate(80 396 738)" text-anchor="middle" font-family="Jost, Arial, sans-serif" font-size="7" font-weight="500" fill="#ffffff" letter-spacing="0.5">STEP 2</text>
  <text x="282" y="850" transform="rotate(-80 282 850)" text-anchor="middle" font-family="Jost, Arial, sans-serif" font-size="7" font-weight="500" fill="#ffffff" letter-spacing="0.5">STEP 3</text>

  <g filter="url(#soft-shadow)">
    <circle cx="335" cy="622" r="30" fill="#fff"/>
    <circle cx="339" cy="740" r="30" fill="#fff"/>
    <circle cx="336" cy="858" r="30" fill="#fff"/>
  </g>

  <!-- upload icon -->
  <g fill="none" stroke="#6b6b6b" stroke-width="2" stroke-linejoin="round">
    <path d="M321 622 L326 614 M349 622 L344 614 M321 622 V631 H349 V622 H340 A5 5 0 0 1 330 622 Z"/>
  </g>
  <path d="M335 606 L328 613 H332 V621 H338 V613 H342 Z" fill="#f37122"/>

  <!-- paper plane icon -->
  <path d="M321 738 L357 726 L345 754 Z" fill="#6b6b6b"/>
  <path d="M357 726 L334 741 L336 752 Z" fill="#f37122"/>
  <path d="M357 726 L334 741 L321 738 Z" fill="#8a8a8a"/>

  <!-- gift icon -->
  <g fill="#6b6b6b">
    <rect x="324" y="852" width="24" height="6"/>
    <rect x="326" y="859" width="20" height="13"/>
  </g>
  <rect x="334" y="852" width="4" height="20" fill="#fff"/>
  <path d="M336 851 C331 843 325 847 331 851 M336 851 C341 843 347 847 341 851" fill="none" stroke="#f37122" stroke-width="2"/>
</svg>

<div class="abs step-text step-1">
  <h3>Upload your resume</h3>
  <p>Answer few questions and upload your resume</p>
</div>
<div class="abs step-text step-2">
  <h3>We Send You Interview Requests</h3>
  <p>Interested in Someone? With a single click,<br>send interview request and let us hondle the rest.</p>
</div>
<div class="abs step-text step-3">
  <h3>Ger $1000 Bonus</h3>
  <p>Find a job and get $1000 bonus TRAVENOK</p>
</div>

<div class="abs btn-upload">
  <svg width="10" height="10" viewBox="0 0 10 10"><path d="M5 0.5 L1.5 4 H3.5 V7 H6.5 V4 H8.5 Z" fill="#fff"/><rect x="0.5" y="8" width="9" height="1.6" fill="#fff"/></svg>
  UPLOAD YOUR RESUME
</div>

<!-- Footer -->
<div class="abs footer"></div>
<div class="abs brand footer-brand">
  <div class="brand-name">TRAVENOK</div>
  <div class="brand-tag">PROJECT MANAGEMENT CONSULTING</div>
</div>

<div class="abs footer-heading" style="left:313px">CONTACT US</div>
<div class="abs contact-row" style="top:1081px">
  <svg width="6" height="8" viewBox="0 0 6 8" style="margin-top:2px"><path d="M3 8 C1 5 0 4 0 3 A3 3 0 0 1 6 3 C6 4 5 5 3 8 Z" fill="#2b2b2b"/><circle cx="3" cy="3" r="1" fill="#f2f2f2"/></svg>
  <span>418 Orchard Bend Lane, San Jose,<br>CA 95120.</span>
</div>
<div class="abs contact-row" style="top:1110px">
  <svg width="7" height="6" viewBox="0 0 7 6" style="margin-top:3px"><rect width="7" height="5" fill="#2b2b2b"/><path d="M0 0.4L3.5 3 7 0.4" fill="none" stroke="#f2f2f2" stroke-width="0.7"/></svg>
  <span>Email: office@travenoktech.example</span>
</div>

<div class="abs footer-heading" style="left:510px">FOLLOW US</div>
<div class="abs social" style="left:510px" aria-label="Social profile"></div>
<div class="abs social" style="left:542px" aria-label="Social profile"></div>
<div class="abs social" style="left:573px" aria-label="Social profile"></div>

<div class="abs footer-rule"></div>
<p class="abs copyright">Copyrihgts @ 2016 All Rights Reserved</p>

</body>
</html>
```